Emergency and Referral Vet Hospital promotional sticker design

We're looking at getting some stickers designed that we could give to clients to put on their cars for promotion and advertising. If they could also be suitable for a goodie bag for conference too that would be great. I like the look of water-colour backgrounds, we'll need to include our logo and probably our address (Unit 3/215 Korrinup Road Tallowmere). We also have a hospital motto "... because they're family" if that could somehow be integrated, we only care for small animals (dogs, cats etc) but the design is very open to suggestion. Would love to see what you can create.

Industry/Entity Type

Veterinary

Colors
0054AA
0677BA
7BADD7
CADEEF
E8F1F8
0094D4
00A9DD
6FCCEA
C7EBF8
E9F6FB

Requirements
Nice to have
• Think beach vibes, blues maybe paw print shapes etc

```html
<!DOCTYPE html>
<html lang="en">
<head>
<meta charset="utf-8">
<title>Tidewell Vet Hospital – Paw Sticker</title>
<link rel="stylesheet" href="https://fonts.googleapis.com/css2?family=Questrial&family=Fira+Sans:ital,wght@1,600&display=swap">
<style>
  :root {
    --canvas-bg: #cbcbcb;
    --sticker-edge: #ffffff;
    --pad-white: #ffffff;
    --water-light: #8ed8e6;
    --water-mid: #22a6c4;
    --water-deep: #0b6f9e;
    --water-dark: #0a4f7e;
    --ink-plum: #2b1a2c;
    --address-cream: #f5ecd6;
    --mark-teal: #1f8fae;
  }
  html, body {
    margin: 0;
    padding: 0;
    overflow: hidden;
    background: var(--canvas-bg);
  }
  .canvas {
    width: 1200px;
    height: 1200px;
    background: var(--canvas-bg);
  }
  .paw-sticker { display: block; width: 1200px; height: 1200px; }
  .sticker-edge { fill: var(--sticker-edge); stroke: var(--sticker-edge); stroke-width: 38; stroke-linejoin: round; }
  .toe-pad, .main-pad { fill: var(--pad-white); }
  .brand-name {
    font-family: "Questrial", sans-serif;
    font-size: 34px;
    letter-spacing: 1px;
    fill: var(--ink-plum);
  }
  .brand-dot { fill: var(--mark-teal); }
  .motto {
    font-family: "Fira Sans", sans-serif;
    font-style: italic;
    font-weight: 600;
    font-size: 19px;
    fill: var(--ink-plum);
  }
  .address {
    font-family: "Questrial", sans-serif;
    font-size: 18px;
    letter-spacing: 0.6px;
    fill: var(--address-cream);
  }
</style>
</head>
<body>
<main class="canvas">
  <svg class="paw-sticker" viewBox="0 0 1465 1465" xmlns="http://www.w3.org/2000/svg">
    <defs>
      <linearGradient id="watercolour-wash" x1="0.35" y1="0" x2="0.6" y2="1">
        <stop offset="0" stop-color="var(--water-light)"/>
        <stop offset="0.3" stop-color="var(--water-mid)"/>
        <stop offset="0.7" stop-color="var(--water-deep)"/>
        <stop offset="1" stop-color="var(--water-dark)"/>
      </linearGradient>
      <path id="paw-outline" d="M 540 605 C 560 520, 640 470, 730 485 C 800 450, 880 490, 915 600 C 990 610, 1020 680, 1008 760 C 1000 820, 970 860, 945 880 C 950 950, 920 995, 860 995 C 800 995, 760 975, 720 985 C 660 1000, 600 1000, 560 975 C 520 950, 515 910, 518 885 C 480 860, 455 810, 460 740 C 465 660, 500 615, 540 605 Z"/>
      <path id="address-arc" d="M 568 948 Q 735 1008 912 956"/>
    </defs>

    <use href="#paw-outline" class="sticker-edge"/>
    <g role="img" aria-label="Blue and teal watercolour wash filling the paw print">
      <use href="#paw-outline" fill="url(#watercolour-wash)"/>
    </g>

    <g class="toes">
      <ellipse class="toe-pad" cx="557" cy="750" rx="50" ry="82"/>
      <ellipse class="toe-pad" cx="660" cy="612" rx="62" ry="86" transform="rotate(-6 660 612)"/>
      <ellipse class="toe-pad" cx="806" cy="605" rx="62" ry="83" transform="rotate(4 806 605)"/>
      <ellipse class="toe-pad" cx="907" cy="745" rx="50" ry="82"/>
    </g>

    <path class="main-pad" d="M 735 720 C 800 720, 840 800, 870 860 C 900 910, 890 945, 840 945 L 630 945 C 585 945, 570 915, 595 870 C 630 800, 670 720, 735 720 Z"/>

    <g class="brand">
      <circle class="brand-dot" cx="672" cy="864" r="9"/>
      <text class="brand-name" x="745" y="876" text-anchor="middle">Tidewell</text>
    </g>
    <text class="motto" x="732" y="908" text-anchor="middle">“… because they’re family”</text>

    <text class="address">
      <textPath href="#address-arc" startOffset="50%" text-anchor="middle">Unit 3/215 Korrinup Road Tallowmere</textPath>
    </text>
  </svg>
</main>
</body>
</html>
```